Restyle corporate identity (+ logo) for a road construction company

We need a new logo and stationary design for our company VARNOK path. VARNOK path® increases the road base strength, while reducing major costs and time of road construction. Attached some examples of the current design.

Our wishes for the new logo:
- Business look
- Style sheet
- Modern

More information: www.varnokpath.example
Updates

Target Market(s)

Government

Industry/Entity Type

Construction

Requirements
Must have
• Logo (with road sign) + text

```html
<!DOCTYPE html>
<html lang="en">
<head>
<meta charset="utf-8">
<title>VARNOK path – Business Card</title>
<link rel="stylesheet" href="https://fonts.googleapis.com/css2?family=Ubuntu:wght@400;500;700&display=swap">
<style>
  :root {
    --backdrop: #8c8c8c;
    --card-white: #f1f1f1;
    --brand-blue: #1a7fe6;
    --back-blue: #127be2;
    --text-dark: #444444;
    --text-grey: #8a8a8a;
    --white: #ffffff;
  }
  * { margin: 0; padding: 0; box-sizing: border-box; }
  html, body {
    width: 1105px; height: 1200px; overflow: hidden;
    background: var(--backdrop);
    font-family: "Ubuntu", sans-serif;
  }
  .stage { position: relative; width: 1105px; height: 1200px; }
  .card {
    position: absolute; left: 182px; width: 746px; height: 425px;
  }
  .card--front { top: 119px; background: var(--card-white); }
  .card--back { top: 637px; background: var(--back-blue); }

  .wordmark {
    position: absolute; left: 0; right: 0; top: 84px;
    display: flex; justify-content: center; align-items: center; gap: 16px;
  }
  .wordmark__square { width: 30px; height: 30px; background: var(--brand-blue); border-radius: 4px; }
  .wordmark__name {
    font-weight: 700; font-size: 54px; letter-spacing: 3px;
    color: var(--brand-blue); line-height: 1;
  }

  .person { position: absolute; left: 0; right: 0; top: 222px; text-align: center; }
  .person__name { font-weight: 500; font-size: 24px; color: var(--brand-blue); letter-spacing: 1px; }
  .person__role { font-size: 18px; color: var(--text-grey); margin-top: 4px; }

  .contact-list { position: absolute; left: 46px; top: 300px; list-style: none; }
  .contact-list li {
    display: flex; align-items: center; gap: 10px;
    font-size: 19px; color: var(--text-dark); height: 28.5px;
  }
  .contact-list svg { width: 17px; height: 17px; fill: var(--brand-blue); }

  .address {
    position: absolute; right: 38px; top: 300px; text-align: right;
    font-style: normal; font-size: 19px; color: var(--text-dark); line-height: 28.5px;
  }

  .edge-tab { position: absolute; top: 282px; width: 12px; height: 117px; background: var(--brand-blue); }
  .edge-tab--left { left: 0; border-radius: 0 8px 8px 0; }
  .edge-tab--right { right: 0; border-radius: 8px 0 0 8px; }

  .back-wordmark {
    position: absolute; left: 0; right: 0; top: 128px; text-align: center;
    font-weight: 700; font-size: 62px; letter-spacing: 4px; color: var(--white); line-height: 1.15;
  }
  .back-url {
    position: absolute; left: 0; right: 0; top: 274px; text-align: center;
    font-size: 20px; letter-spacing: 2px; color: var(--white);
  }
</style>
</head>
<body>
<main class="stage">
  <section class="card card--front">
    <div class="wordmark">
      <span class="wordmark__square"></span>
      <span class="wordmark__name">VARNOK PATH</span>
    </div>

    <div class="person">
      <p class="person__name">MAREN VELLEKOOP</p>
      <p class="person__role">CEO/Founder</p>
    </div>

    <span class="edge-tab edge-tab--left"></span>
    <span class="edge-tab edge-tab--right"></span>

    <ul class="contact-list">
      <li>
        <svg viewBox="0 0 24 24" aria-hidden="true"><path d="M6.6 10.8a15.1 15.1 0 0 0 6.6 6.6l2.2-2.2a1 1 0 0 1 1-.25 11.4 11.4 0 0 0 3.6.57 1 1 0 0 1 1 1V20a1 1 0 0 1-1 1A17 17 0 0 1 3 4a1 1 0 0 1 1-1h3.5a1 1 0 0 1 1 1c0 1.25.2 2.45.57 3.6a1 1 0 0 1-.25 1z"/></svg>
        612 480 3391
      </li>
      <li>
        <svg viewBox="0 0 24 24" aria-hidden="true"><path d="M2 5h20v14H2z M3 6l9 7 9-7" fill-rule="evenodd"/><path d="M2 5l10 8 10-8v2l-10 8L2 7z" fill="#f1f1f1"/></svg>
        contact@varnokpath.example
      </li>
      <li>
        <svg viewBox="0 0 24 24" aria-hidden="true"><circle cx="12" cy="12" r="10"/><path d="M2 12h20M12 2c3 3 3 17 0 20M12 2c-3 3-3 17 0 20" stroke="#f1f1f1" stroke-width="1.5" fill="none"/></svg>
        www.varnokpath.example
      </li>
    </ul>

    <address class="address">
      Brenkelplein 27<br>
      3417 KV Ostervaal<br>
      The Netherlands
    </address>
  </section>

  <section class="card card--back">
    <p class="back-wordmark">VARNOK<br>PATH</p>
    <p class="back-url">www.varnokpath.example</p>
  </section>
</main>
</body>
</html>
```